LEARN Business Skills so you can Earn a good living

size of the poster is 8”x 10.75" plus 0.25" bleed.
Please leave 1 inch on the bottoum for footer
I want a design a poster that will attract people's attention.
I appreciate a creative ad however the ad should not take away from being able to clearly read the text.
-I also appreciate a simple creative ad that is not too busy.
-you can use graphics, vectors, or pictures of real people.
-however, if you use real people it should be a white male that is wearing a white shirt and look like a professional person.

Target Market(s)

Potential young business people

Industry/Entity Type

education

Requirements
Must have
• easy to read the text
Nice to have
• I would like a "creative" simple ad that is easy to be read
Should not have
• pictures of women

```html
<!DOCTYPE html>
<html lang="en">
<head>
<meta charset="utf-8">
<title>Build to Thrive – Business Enrichment Course</title>
<link href="https://fonts.googleapis.com/css2?family=Montserrat:wght@300;400;500;700;800&family=Roboto+Condensed:wght@400;700&display=swap" rel="stylesheet">
<style>
  :root{
    --red:#ec1f27;
    --yellow:#fff200;
    --white:#ffffff;
    --navy:#1f3468;
    --slate:#3f4f82;
    --ink:#1b1b1b;
    --sky:#1cc0ef;
    --rule-dark:#2f3f7a;
  }
  *{margin:0;padding:0;box-sizing:border-box}
  html,body{width:893px;height:1200px;overflow:hidden;background:var(--white)}
  .poster{position:relative;width:893px;height:1200px;background:var(--white);font-family:'Montserrat',sans-serif}
  .taglines{position:absolute;top:32px;left:0;width:100%;text-align:center;color:var(--slate);font-weight:300;font-size:28px;line-height:35px}
  .hero,.topics{position:absolute;left:0;top:0}
  .footer-rule{position:absolute;top:1091px;height:5px}
  .footer-rule--light{left:0;width:444px;background:var(--sky)}
  .footer-rule--dark{left:448px;width:445px;background:var(--rule-dark)}
  .org-mark{position:absolute;left:6px;top:1108px;width:166px;text-align:center;color:var(--navy);white-space:nowrap}
  .org-mark__name{display:flex;align-items:center;justify-content:center;gap:8px;font-size:36px;font-weight:500;line-height:40px}
  .org-mark__dot{width:22px;height:22px;border-radius:50%;background:var(--sky)}
  .org-mark__full{font-size:11px;font-weight:500;margin-top:8px}
  .org-mark__services{font-size:9.5px;color:var(--ink);margin-top:3px}
  .placement-badge{position:absolute;left:178px;top:1104px;width:108px;height:85px;background:var(--navy);border-radius:10px;color:var(--white);text-align:center;padding-top:8px;font-weight:800}
  .placement-badge__count{font-size:23px;line-height:22px}
  .placement-badge__unit{font-size:20px;line-height:20px}
  .placement-badge__label{font-size:11px;font-weight:700;margin-top:4px}
  .contact{position:absolute;left:295px;top:1107px;width:400px;font-family:'Roboto Condensed',sans-serif;font-size:16px;line-height:26px;color:var(--ink);white-space:nowrap}
  .contact b{font-weight:700}
  .divider{position:absolute;left:706px;top:1106px;height:82px;border-left:1px dashed #9a9a9a}
  .sponsor{position:absolute;left:716px;top:1104px;width:174px;text-align:center;font-family:'Roboto Condensed',sans-serif;color:var(--ink)}
  .sponsor__label{font-size:15px}
  .sponsor__name{display:flex;align-items:center;gap:8px;margin-top:10px;padding-left:6px;font-family:'Montserrat',sans-serif;font-weight:700;font-size:15px;line-height:17px;color:var(--navy);text-align:left}
  .sponsor__square{flex:none;width:30px;height:30px;background:var(--navy)}
</style>
</head>
<body>
<main class="poster">

  <div class="taglines">
    <p>“In-person lkwd &amp; remote”</p>
    <p>“Limited partial scholarships”</p>
  </div>

  <svg class="hero" width="893" height="1200" viewBox="0 0 893 1200" aria-label="Build to Thrive – Business Enrichment Course">
    <circle cx="446" cy="490" r="352" fill="var(--red)"/>
    <g font-family="Montserrat, sans-serif" font-weight="800">
      <text x="446" y="395" font-size="133" fill="var(--white)" text-anchor="middle" textLength="420" lengthAdjust="spacingAndGlyphs">BUILD</text>
      <text x="200" y="512" font-size="66" fill="var(--yellow)" textLength="71" lengthAdjust="spacingAndGlyphs">to</text>
      <text x="280" y="512" font-size="133" fill="var(--white)" textLength="420" lengthAdjust="spacingAndGlyphs">THRIVE</text>
    </g>
    <g font-family="Montserrat, sans-serif" text-anchor="middle">
      <text x="446" y="582" font-size="44" font-weight="800" fill="var(--yellow)" textLength="578" lengthAdjust="spacingAndGlyphs">Business Enrichment Course</text>
      <text x="446" y="630" font-size="31" font-weight="400" fill="var(--white)" textLength="498" lengthAdjust="spacingAndGlyphs">A proven success of helping people</text>
      <text x="446" y="674" font-size="30" font-weight="800" fill="var(--white)">Get a Quality Job</text>
      <text x="446" y="720" font-size="30" font-weight="800" fill="var(--white)">Start / Grow a Business</text>
      <text x="446" y="767" font-size="30" font-weight="800" fill="var(--white)">Increase Salary</text>
    </g>
  </svg>

  <svg class="topics" width="893" height="1200" viewBox="0 0 893 1200" aria-label="Course topics">
    <g font-family="Montserrat, sans-serif" font-weight="500" font-size="13" fill="var(--ink)" text-anchor="middle">
      <text x="446" y="1007" textLength="702" lengthAdjust="spacingAndGlyphs">BUSINESS ADMIISTRATION <tspan fill="var(--red)">–</tspan> SMALL BUSINESS MANAGEMENT <tspan fill="var(--red)">–</tspan> FINANCE <tspan fill="var(--red)">–</tspan> INVESTMENTS <tspan fill="var(--red)">–</tspan> COMPUTERS</text>
      <text x="446" y="1028" textLength="706" lengthAdjust="spacingAndGlyphs">ACCOUNTING <tspan fill="var(--red)">–</tspan> SALES <tspan fill="var(--red)">–</tspan> MARKETING <tspan fill="var(--red)">–</tspan> PROJECT MANAGEMENT <tspan fill="var(--red)">–</tspan> INTERVIEWING SKILLS <tspan fill="var(--red)">–</tspan> BUSINESS LAW</text>
      <text x="446" y="1049" textLength="668" lengthAdjust="spacingAndGlyphs">NEGOTIATION <tspan fill="var(--red)">–</tspan> PUBLIC SPEAKING <tspan fill="var(--red)">–</tspan> IMPORT/EXPORT <tspan fill="var(--red)">–</tspan> INFORMATION TECHNOLOY <tspan fill="var(--red)">–</tspan> DISTRIBUTION</text>
      <text x="446" y="1070" textLength="636" lengthAdjust="spacingAndGlyphs">MARKETING <tspan fill="var(--red)">–</tspan> LEDGERLY <tspan fill="var(--red)">–</tspan> REAL ESTATE <tspan fill="var(--red)">–</tspan> HEALTH CARE <tspan fill="var(--red)">–</tspan> BUSINESS STRATEGY <tspan fill="var(--red)">–</tspan> E-COMMERCE</text>
    </g>
  </svg>

  <div class="footer-rule footer-rule--light"></div>
  <div class="footer-rule footer-rule--dark"></div>

  <div class="org-mark">
    <div class="org-mark__name"><span class="org-mark__dot"></span>NCT</div>
    <div class="org-mark__full">NORTHLINE CAREER TRUST</div>
    <div class="org-mark__services">placement | counseling | training</div>
  </div>

  <div class="placement-badge">
    <div class="placement-badge__count">7,000+</div>
    <div class="placement-badge__unit">JOB</div>
    <div class="placement-badge__label">PLACEMENTS</div>
  </div>

  <div class="contact">
    <p><b>Call:</b> 555 014 2200 x 12</p>
    <p><b>E-mail:</b> info@northlinecareer.org</p>
    <p>NCT is sponsored in part by the Harlan Brookfield Foundation</p>
  </div>

  <div class="divider"></div>

  <div class="sponsor">
    <div class="sponsor__label">Sponsored in part</div>
    <div class="sponsor__name"><span class="sponsor__square"></span><span>Meridian Care<br>Alliance</span></div>
  </div>

</main>
</body>
</html>
```